Hunting club needs a new web design !

We need a new web design for our hunting club located in Poland, called "BORYNA". The club was founded in 1945. Colors that we would like to see in the project are the colors of the forest. The website should be built in such a way that all text elements can be changed to another language and can't be graphic.
"BORYNA" means - big, thick forest in which the game, small and big resides

Target Market(s)

hunters,

Industry/Entity Type

Hunting

Coding

Coded - Design and coding required

Number of Pages Required

5+ page

Font styles to use
Decorative

Colors

Designer to choose colors to be used in the design.

Requirements
Must have
• current date, calendar,
• must contain almost all materials from our current web page
• http://boryna-lasowiec.webnest.pl/
• new web address: borynalsw.pl
Nice to have
• current weather in three hunting regions that we allowed to hunt, or indicated by the visitor on the map placed on our web,
• actual phase of the moon, actual moon rising hour, actual moon set hour, actual sun rise hour, actual sun set hour, current weather in region (stalowa wola, poland)
• wood, forest, deers, boars,
Should not have
• mountain photos, modern look, white or bright backgrounds,

```html
<!DOCTYPE html>
<html lang="en">
<head>
<meta charset="utf-8">
<title>BORYNA Hunting Club</title>
<link rel="stylesheet" href="https://fonts.googleapis.com/css2?family=Lato:wght@400;700;900&family=Open+Sans:wght@400;600;700&display=swap">
<style>
:root{
  --green:#7ac143;
  --green-dark:#5e9f2c;
  --brown:#4a2a1a;
  --brown-deep:#3a2216;
  --footer:#2b231f;
  --text:#555;
  --heading:#222;
  --white:#fff;
  --cell:#dcdcdc;
  --line:#e2e2e2;
}
*{box-sizing:border-box;margin:0;padding:0}
html,body{width:1200px;height:2439px;overflow:hidden}
body{font-family:"Open Sans",Arial,sans-serif;color:var(--text);background:var(--white);position:relative}
.abs{position:absolute}

/* hero */
.hero{position:absolute;left:0;top:0;width:1200px;height:528px}
.hero-photo{position:absolute;inset:0;background:linear-gradient(180deg,#2c2a22 0%,#6b5a35 12%,#c98a3a 20%,#6a7048 32%,#3f6a2c 55%,#4f8a2a 80%,#3a6a1e 100%)}
.brand{position:absolute;left:98px;top:16px;display:flex;align-items:center;gap:10px;color:var(--white);font-family:"Lato",sans-serif;font-weight:900;font-size:30px;letter-spacing:1px}
.brand-dot{width:34px;height:34px;border-radius:50%;background:var(--white)}
.contact-top{position:absolute;top:30px;display:flex;gap:14px;align-items:center;color:var(--white)}
.contact-top .ico{width:40px;height:40px;border:2px solid var(--white);border-radius:50%;display:flex;align-items:center;justify-content:center}
.contact-top small{display:block;font-size:13px;font-weight:600}
.contact-top b{display:block;font-size:17px;font-weight:700;margin-top:2px}
.nav{position:absolute;left:0;top:113px;width:1200px;height:37px;border-top:1.5px solid rgba(255,255,255,.85);border-bottom:1.5px solid rgba(255,255,255,.85);display:flex;justify-content:center;gap:26px;align-items:center}
.nav a{color:var(--white);text-decoration:none;font-family:"Lato",sans-serif;font-weight:700;font-size:15px}
.hero-title{position:absolute;left:0;width:1200px;top:225px;text-align:center;color:var(--white);font-family:"Lato",sans-serif;font-weight:700;font-size:48px;line-height:60px;text-shadow:0 2px 6px rgba(0,0,0,.35)}
.hero-title em{font-style:normal;color:var(--green)}
.dots{position:absolute;top:461px;left:566px;display:flex;gap:5px}
.dots span{width:13px;height:13px;border-radius:50%;border:2px solid var(--white)}
.dots span:first-child{background:var(--white)}

/* welcome */
.welcome h1{position:absolute;left:97px;top:594px;font-family:"Lato",sans-serif;font-weight:700;font-size:30px;color:var(--heading)}
.welcome p{position:absolute;left:97px;width:600px;font-size:14px;line-height:26px;color:#666}
.btn-outline{position:absolute;left:98px;top:847px;width:127px;height:38px;border:1.5px solid #999;border-radius:20px;color:var(--green);font-weight:700;font-size:12px;display:flex;align-items:center;justify-content:center}

/* calendar */
.calendar{position:absolute;left:748px;top:564px;width:354px;height:330px;border:1.5px solid var(--line);background:var(--white)}
.cal-pin{position:absolute;width:3px;height:40px;background:#ccc;top:-40px}
.cal-head{position:absolute;left:22px;top:3px;width:310px;height:44px;background:var(--brown);color:var(--white);font-family:"Lato",sans-serif;font-weight:700;font-size:20px;display:flex;align-items:center;justify-content:center}
.cal-head .knob{position:absolute;width:18px;height:18px;border-radius:50%;background:#ddd;top:13px}
.cal-head .arr{position:absolute;top:15px;width:0;height:0;border-top:7px solid transparent;border-bottom:7px solid transparent}
.cal-grid{position:absolute;left:22px;top:62px;display:grid;grid-template-columns:repeat(7,40px);gap:5px;font-size:18px;color:#333}
.cal-grid .dow{text-align:center;font-weight:700;height:28px}
.cal-grid .d{height:40px;background:var(--cell);display:flex;align-items:center;justify-content:center}
.cal-grid .e{height:40px}
.cal-grid .today{background:var(--green);color:var(--white)}

/* stats */
.stats{position:absolute;left:0;top:976px;width:1200px;height:344px;background:linear-gradient(180deg,#1b2434 0%,#2c3240 40%,#5a4a3a 70%,#2a2520 100%)}
.stat{position:absolute;top:60px;width:175px;text-align:center;color:var(--white)}
.stat .ring{width:124px;height:124px;margin:0 auto;border:3px solid var(--white);border-radius:50%;display:flex;align-items:center;justify-content:center}
.stat .val{font-family:"Lato",sans-serif;font-weight:700;font-size:24px;margin-top:14px}
.stat .lbl{font-size:16px;line-height:22px;margin-top:2px}

/* moon phases */
.moon-box{position:absolute;left:99px;top:1442px;width:1002px;height:176px;border:1.5px solid var(--brown)}
.moon-tab{position:absolute;left:463px;top:1416px;width:274px;height:52px;background:var(--brown);color:var(--white);font-family:"Lato",sans-serif;font-weight:700;font-size:28px;display:flex;align-items:center;justify-content:center}
.field{position:absolute;top:1497px;width:281px}
.field label{display:block;font-size:12px;color:#666;margin-bottom:8px}
.field .inp{height:39px;border:1.5px solid #ccc;display:flex;align-items:center;padding-left:12px}
.btn-green{position:absolute;left:537px;top:1597px;width:128px;height:44px;border-radius:22px;background:var(--green);color:var(--white);font-weight:700;font-size:15px;display:flex;align-items:center;justify-content:center}

/* map */
.map{position:absolute;left:0;top:1737px;width:1200px;height:349px;background:linear-gradient(135deg,#e6e6e4,#dcdcd8 50%,#e4e4e1)}
.map-title{position:absolute;left:0;width:1200px;top:1802px;text-align:center;font-family:"Lato",sans-serif;font-weight:900;font-size:30px;color:var(--brown)}
.pin{position:absolute;width:58px;height:58px;border-radius:50%;background:rgba(122,193,67,.45);display:flex;align-items:center;justify-content:center}
.pin span{width:36px;height:36px;border-radius:50%;background:var(--green);display:flex;align-items:center;justify-content:center}

/* footer */
.footer{position:absolute;left:0;top:2086px;width:1200px;height:353px;background:var(--footer);color:var(--white)}
.footer .brand{left:98px;top:78px}
.footer h4{position:absolute;top:66px;font-size:16px;font-weight:600}
.links{position:absolute;left:346px;top:100px;list-style:none;font-size:12.5px;line-height:19px}
.news p{position:absolute;left:551px;top:100px;width:250px;font-size:12.5px;line-height:20px}
.news .email{position:absolute;left:551px;top:153px;width:254px;height:35px;background:var(--white);color:#555;font-size:12px;display:flex;align-items:center;padding-left:14px}
.news .sub{position:absolute;left:553px;top:210px;width:101px;height:31px;border-radius:16px;background:var(--green);font-size:11px;display:flex;align-items:center;justify-content:center}
.contact-list{position:absolute;left:880px;top:106px;list-style:none;font-size:12.5px;line-height:19px}
.contact-list li{display:flex;gap:14px;margin-bottom:22px}
.contact-list li svg{margin-top:3px;flex:none}
.divider{position:absolute;left:99px;top:284px;width:1002px;height:1px;background:#4a403a}
.copy{position:absolute;left:99px;top:318px;font-size:12px}
.social{position:absolute;left:975px;top:311px;display:flex;gap:7px}
.social span{width:26px;height:26px;border:1.5px solid var(--white);border-radius:50%}
</style>
</head>
<body>

<header class="hero">
  <div class="hero-photo" role="img" aria-label="Sunset over a forested valley"></div>
  <div class="brand"><span class="brand-dot"></span>BORYNA</div>
  <div class="contact-top" style="left:568px">
    <div class="ico"><svg width="18" height="18" viewBox="0 0 24 24"><path fill="#fff" d="M6.6 10.8a15 15 0 0 0 6.6 6.6l2.2-2.2c.3-.3.7-.4 1-.2 1.1.4 2.3.6 3.6.6.6 0 1 .4 1 1V20c0 .6-.4 1-1 1A17 17 0 0 1 3 4c0-.6.4-1 1-1h3.5c.6 0 1 .4 1 1 0 1.3.2 2.5.6 3.6.1.3 0 .7-.2 1z"/></svg></div>
    <div><small>Call Us:</small><b>1 555 010 2040</b></div>
  </div>
  <div class="contact-top" style="left:782px">
    <div class="ico" style="background:var(--green);border-color:var(--green)"><svg width="18" height="14" viewBox="0 0 18 14"><rect width="18" height="14" rx="2" fill="#fff"/><path d="M1 2l8 6 8-6" stroke="#7ac143" stroke-width="1.6" fill="none"/></svg></div>
    <div><small>Email Us:</small><b>info@boryna-lasowiec.webnest.pl</b></div>
  </div>
  <nav class="nav">
    <a>History of Kola</a><a>Kola Management</a><a>Equipment of hunting</a><a>Ethics of the Lukers</a><a>Hunting Plan</a><a>Polovia Calendar</a><a>Cynology</a><a>Nowosi</a><a>Gallery</a>
  </nav>
  <h2 class="hero-title">Honorary Merit Badge <em>"ZLOM"</em> and<br>the Medal of Holy Hubert</h2>
  <div class="dots"><span></span><span></span><span></span><span></span></div>
</header>

<section class="welcome">
  <h1>WELCOME TO BORYNA WHEELS</h1>
  <p style="top:652px">We hope you forward the message They will make it easier for all hunters and hunters Getting to know the scope and problems of our Circle.</p>
  <p style="top:730px">The beginnings can be difficult, but we believe that over time. We will be able to expand our site with other interesting topics from our business. Clients of hunters KŁ BORYNA please look at the tab NEW, In which the current information and messages will be posted.</p>
  <div class="btn-outline">READ MORE &gt;&gt;</div>
</section>

<aside class="calendar">
  <span class="cal-pin" style="left:72px"></span><span class="cal-pin" style="left:278px"></span>
  <div class="cal-head">
    <span class="arr" style="left:14px;border-right:9px solid #fff"></span>
    <span class="knob" style="left:42px"></span>
    August 2017
    <span class="knob" style="left:250px"></span>
    <span class="arr" style="right:14px;border-left:9px solid #fff"></span>
  </div>
  <div class="cal-grid">
    <div class="dow">Su</div><div class="dow">Mo</div><div class="dow">Tu</div><div class="dow">We</div><div class="dow">Th</div><div class="dow">Fr</div><div class="dow">Sa</div>
    <div class="e"></div><div class="e"></div><div class="d">1</div><div class="d">2</div><div class="d">3</div><div class="d">4</div><div class="d">5</div>
    <div class="d">6</div><div class="d">7</div><div class="d">8</div><div class="d">9</div><div class="d">10</div><div class="d">11</div><div class="d">12</div>
    <div class="d">13</div><div class="d">14</div><div class="d">15</div><div class="d">16</div><div class="d">17</div><div class="d today">18</div><div class="d">19</div>
    <div class="d">20</div><div class="d">21</div><div class="d">22</div><div class="d">23</div><div class="d">24</div><div class="d">25</div><div class="d">26</div>
    <div class="d">27</div><div class="d">28</div><div class="d">29</div><div class="d">30</div><div class="d">30</div><div class="d"></div>
  </div>
</aside>

<section class="stats">
  <div class="abs" style="inset:0" role="img" aria-label="Night sky over a mountain ridge"></div>
  <div class="stat" style="left:74px"><div class="ring"><svg width="64" height="64" viewBox="0 0 64 64"><circle cx="32" cy="32" r="30" fill="#7ac143"/><g fill="none" stroke="#2c3a1a" stroke-width="2"><circle cx="22" cy="36" r="6"/><circle cx="38" cy="46" r="5"/><circle cx="42" cy="22" r="4"/><circle cx="28" cy="18" r="3"/></g></svg></div><div class="val">100%</div><div class="lbl">Actual phase of<br>the moon</div></div>
  <div class="stat" style="left:250px"><div class="ring"><svg width="70" height="60" viewBox="0 0 70 60"><path d="M28 4a22 22 0 1 0 22 30A18 18 0 0 1 28 4z" fill="#7ac143"/><path d="M24 56h34a10 10 0 0 0-2-20 14 14 0 0 0-26 4 8 8 0 0 0-6 16z" fill="#7ac143" stroke="#2c3240" stroke-width="2"/></svg></div><div class="val">23:56:60</div><div class="lbl">Actual moon<br>rising hour</div></div>
  <div class="stat" style="left:425px"><div class="ring"><svg width="70" height="60" viewBox="0 0 70 60"><path d="M36 6a16 16 0 1 0 14 24A13 13 0 0 1 36 6z" fill="#7ac143"/><rect x="8" y="38" width="54" height="4" fill="#7ac143"/><rect x="14" y="46" width="42" height="4" fill="#7ac143"/><rect x="20" y="54" width="30" height="4" fill="#7ac143"/></svg></div><div class="val">18:56:60</div><div class="lbl">Actual moon<br>set hour</div></div>
  <div class="stat" style="left:601px"><div class="ring"><svg width="70" height="60" viewBox="0 0 70 60"><g stroke="#7ac143" stroke-width="3"><path d="M42 4v8M56 12l-5 5M28 12l5 5M64 26h-7"/></g><circle cx="42" cy="28" r="10" fill="#7ac143"/><path d="M14 54h40a11 11 0 0 0-2-22 15 15 0 0 0-28 4 9 9 0 0 0-10 18z" fill="#7ac143" stroke="#2c3240" stroke-width="2"/></svg></div><div class="val">19:22:12</div><div class="lbl">Actual sun<br>rise hour</div></div>
  <div class="stat" style="left:776px"><div class="ring"><svg width="70" height="50" viewBox="0 0 70 50"><path d="M15 40a20 20 0 0 1 40 0z" fill="#7ac143"/><g stroke="#7ac143" stroke-width="3"><path d="M35 4v10M12 14l7 7M58 14l-7 7M2 32h9M59 32h9"/></g><rect x="4" y="44" width="62" height="4" fill="#7ac143"/></svg></div><div class="val">10:56:60</div><div class="lbl">Actual sun<br>set hour</div></div>
  <div class="stat" style="left:949px"><div class="ring"><svg width="70" height="64" viewBox="0 0 70 64"><g stroke="#7ac143" stroke-width="3"><path d="M44 2v7M57 9l-5 5M64 22h-7"/></g><circle cx="44" cy="24" r="9" fill="#7ac143"/><path d="M14 48h40a11 11 0 0 0-2-22 15 15 0 0 0-28 4 9 9 0 0 0-10 18z" fill="#7ac143" stroke="#2c3240" stroke-width="2"/><path d="M34 42c-4 6-6 9-6 12a6 6 0 0 0 12 0c0-3-2-6-6-12z" fill="#2c3240"/></svg></div><div class="val">23:56:60</div><div class="lbl">Current weather<br>in region</div></div>
</section>

<section class="moon">
  <div class="moon-box"></div>
  <div class="moon-tab">MOON PHASES</div>
  <div class="field" style="left:145px"><label>YEAR:</label><div class="inp"><svg width="12" height="12" viewBox="0 0 12 12"><rect x="1" y="2" width="10" height="9" fill="#bbb"/></svg></div></div>
  <div class="field" style="left:460px"><label>MONTH:</label><div class="inp"><svg width="12" height="12" viewBox="0 0 12 12"><rect x="1" y="2" width="10" height="9" fill="#bbb"/></svg></div></div>
  <div class="field" style="left:774px"><label>DAY:</label><div class="inp"><svg width="12" height="12" viewBox="0 0 12 12"><rect x="1" y="2" width="10" height="9" fill="#bbb"/></svg></div></div>
  <div class="btn-green">SUBMIT</div>
</section>

<section>
  <div class="map" role="img" aria-label="Road map of the three hunting regions"></div>
  <h3 class="map-title">CURRENT WEATHER IN THREE HUNTING REGIONS</h3>
  <div class="pin" style="left:291px;top:1878px"><span><svg width="14" height="18" viewBox="0 0 14 18"><path d="M7 0a7 7 0 0 0-7 7c0 5 7 11 7 11s7-6 7-11a7 7 0 0 0-7-7z" fill="#fff"/><circle cx="7" cy="7" r="2.5" fill="#7ac143"/></svg></span></div>
  <div class="pin" style="left:656px;top:1922px"><span><svg width="14" height="18" viewBox="0 0 14 18"><path d="M7 0a7 7 0 0 0-7 7c0 5 7 11 7 11s7-6 7-11a7 7 0 0 0-7-7z" fill="#fff"/><circle cx="7" cy="7" r="2.5" fill="#7ac143"/></svg></span></div>
  <div class="pin" style="left:880px;top:1900px"><span><svg width="14" height="18" viewBox="0 0 14 18"><path d="M7 0a7 7 0 0 0-7 7c0 5 7 11 7 11s7-6 7-11a7 7 0 0 0-7-7z" fill="#fff"/><circle cx="7" cy="7" r="2.5" fill="#7ac143"/></svg></span></div>
</section>

<footer class="footer">
  <div class="brand"><span class="brand-dot"></span>BORYNA</div>
  <h4 style="left:346px">QUICK LINKS</h4>
  <ul class="links"><li>History of Kola</li><li>Kola Management</li><li>Equipment of hunting</li><li>Ethics of the Lukers</li><li>Hunting Plan</li><li>Polovia Calendar</li><li>Cynology</li><li>Nowosi</li><li>Gallery</li></ul>
  <h4 style="left:551px">NEWSLETTER SUBSCRIPTION</h4>
  <div class="news">
    <p>Register your Email Address to get Information about us</p>
    <div class="email">Email Address</div>
    <div class="sub">SUBSCRIBE</div>
  </div>
  <h4 style="left:880px">CONTACT US</h4>
  <ul class="contact-list">
    <li><svg width="12" height="15" viewBox="0 0 14 18"><path d="M7 0a7 7 0 0 0-7 7c0 5 7 11 7 11s7-6 7-11a7 7 0 0 0-7-7z" fill="#fff"/><circle cx="7" cy="7" r="2.5" fill="#2b231f"/></svg><span>Lindenweg 12, 4120 AB Veldhoven<br>Nederland</span></li>
    <li><svg width="13" height="13" viewBox="0 0 24 24"><path fill="#fff" d="M6.6 10.8a15 15 0 0 0 6.6 6.6l2.2-2.2c.3-.3.7-.4 1-.2 1.1.4 2.3.6 3.6.6.6 0 1 .4 1 1V20c0 .6-.4 1-1 1A17 17 0 0 1 3 4c0-.6.4-1 1-1h3.5c.6 0 1 .4 1 1 0 1.3.2 2.5.6 3.6.1.3 0 .7-.2 1z"/></svg><span>1 555 010 2040</span></li>
    <li><svg width="14" height="11" viewBox="0 0 18 14"><rect width="18" height="14" rx="2" fill="#fff"/><path d="M1 2l8 6 8-6" stroke="#2b231f" stroke-width="1.6" fill="none"/></svg><span>info@boryna-lasowiec.webnest.pl</span></li>
  </ul>
  <div class="divider"></div>
  <p class="copy">Copyrights © 2017, Boryna-Lasowiec.&nbsp; All rights reserved.</p>
  <div class="social"><span></span><span></span><span></span><span></span></div>
</footer>

</body>
</html>
```